design a construction company business card

Design business card around our logo. Card must have all the typical info: name, title, address, phone, email, business name, etc. Somewhere on the card I would like to see our motto "Built on integrity... Inspired by commitment." Consider adding a splash of bright orange to the card to complement the blues and silvers/grays in the logo. We are open to metallic inks, textures, etc. We would like to see options on both light and dark backgrounds. The font in the logo is Euro Technic Extended Regular.

```html
<!DOCTYPE html>
<html lang="en">
<head>
<meta charset="utf-8">
<title>Corwin Contracting, Inc. – Business Card</title>
<link href="https://fonts.googleapis.com/css2?family=Lato:wght@400;700&family=Roboto+Condensed:wght@400&display=swap" rel="stylesheet">
<style>
  :root {
    --stage: #676767;
    --card-light: #efe7e7;
    --brand-blue: #1c5aa8;
    --blue-top: #1a70bb;
    --blue-bottom: #283f93;
    --ink-gray: #666262;
    --rule-gray: #c9c2c2;
    --white: #ffffff;
  }
  * { margin: 0; padding: 0; box-sizing: border-box; }
  html, body { width: 1200px; height: 900px; overflow: hidden; }
  body {
    background: var(--stage);
    position: relative;
    font-family: "Lato", sans-serif;
  }
  .card {
    position: absolute;
    width: 477px;
    height: 292px;
  }
  .card--front {
    left: 120px; top: 275px;
    background: var(--card-light);
    border-radius: 0 46px 0 46px;
  }
  .card--back {
    left: 620px; top: 277px;
    height: 291px;
    background: linear-gradient(180deg, var(--blue-top), var(--blue-bottom));
    border-radius: 46px 0 46px 0;
  }
  .wordmark {
    position: absolute;
    text-align: center;
    text-transform: uppercase;
    font-family: "Lato", sans-serif;
    font-weight: 700;
    line-height: 1;
  }
  .card--front .wordmark {
    left: 30px; width: 190px; top: 128px;
    color: var(--brand-blue);
  }
  .card--front .wordmark__name { font-size: 34px; letter-spacing: 3px; display: block; }
  .card--front .wordmark__suffix { font-size: 12px; letter-spacing: 0.5px; display: block; margin-top: 6px; }
  .card--back .wordmark {
    left: 90px; width: 297px; top: 120px;
    color: var(--white);
  }
  .card--back .wordmark__name { font-size: 54px; letter-spacing: 6px; display: block; }
  .card--back .wordmark__suffix { font-size: 18px; letter-spacing: 1px; display: block; margin-top: 10px; }
  .divider {
    position: absolute;
    left: 238px; top: 85px;
    width: 1px; height: 125px;
    background: var(--rule-gray);
  }
  .contact {
    position: absolute;
    left: 259px; top: 80px;
    color: var(--ink-gray);
    text-transform: uppercase;
  }
  .contact__name { font-size: 17.5px; font-weight: 700; color: var(--brand-blue); line-height: 20px; }
  .contact__title { font-size: 12px; line-height: 14px; }
  .contact__list { list-style: none; margin-top: 8px; }
  .contact__item { font-size: 12.5px; line-height: 18.5px; display: flex; align-items: center; gap: 4px; }
  .contact__item svg { width: 11px; height: 11px; fill: var(--brand-blue); }
  .contact__address { font-size: 12.5px; line-height: 15px; margin-top: 7px; }
  .motto {
    position: absolute;
    left: 0; width: 100%; top: 221px;
    padding-left: 102px;
    color: var(--white);
    font-family: "Roboto Condensed", sans-serif;
    font-size: 12.5px;
    text-transform: uppercase;
  }
</style>
</head>
<body>
  <section class="card card--front" aria-label="Business card front">
    <div class="wordmark">
      <span class="wordmark__name">Corwin</span>
      <span class="wordmark__suffix">Contracting, Inc.</span>
    </div>
    <div class="divider"></div>
    <div class="contact">
      <p class="contact__name">Daniel Harper</p>
      <p class="contact__title">Managing Director</p>
      <ul class="contact__list">
        <li class="contact__item">
          <svg viewBox="0 0 12 12" aria-hidden="true"><path d="M1 4c0-2 1.5-3 5-3s5 1 5 3v1H8.5V3.8h-5V5H1zM3 6h6l2 4H1z"/></svg>
          044-987 654 321
        </li>
        <li class="contact__item">
          <svg viewBox="0 0 12 12" aria-hidden="true"><path d="M1 2.5h10v7H1zM1.8 3.2 6 6.4l4.2-3.2z" fill-rule="evenodd"/></svg>
          info@webname.com
        </li>
        <li class="contact__item">
          <svg viewBox="0 0 12 12" aria-hidden="true"><circle cx="6" cy="6" r="5.5"/></svg>
          www.websitename.com
        </li>
      </ul>
      <p class="contact__address">421, Address Line Here<br>Country Name, 45452</p>
    </div>
  </section>

  <section class="card card--back" aria-label="Business card back">
    <div class="wordmark">
      <span class="wordmark__name">Corwin</span>
      <span class="wordmark__suffix">Contracting, Inc.</span>
    </div>
    <p class="motto">Built on integrity... Inspired by commitment</p>
  </section>
</body>
</html>
```